New, modern business card for growing audiology practice

We need a new business card for our audiology practice. Our logo and website have recently changed (more modern) and we want our business cards to reflect this change.
We conduct hearing tests, perform earwax removals, and fit & dispense hearing aids to our patients. We are a family owned practice in which the owner is the one who works directly with the patient. I have attached logos in various formats to use, as well as two ideas I found on this website; as well as a scanned copy of our current logo. Good luck!

Industry/Entity Type

Business

Contact Information for Business Card

Company name: Tolvera Hearing Center
Provider name: Peter Wolstenby, Au.D. F/NSB
Phone number: (440) 683-5127
Address: 837 W. Lindell Ave. Brenhurst, OH 44091
email: tolverahearing@postvane.com
website: tolverahearing.com

Colors
000000
aaaaaa
dbdbdb
cacaca
9bcb3c
afd23c
cadf82
b1b1b1

Requirements
Must have
• My card must include information in the "details" section. In the attached images, I found a few that I liked and I would like to model after - "brisky bouncin'" and "Sound Method Center".
• Must be horizontal.
• Must include logos provided. I uploaded them in various file formats and various ways.
• Must match logo font, if possible, if not, please get as close as you can.
Nice to have
• I really like the idea of having a color on one side with just the logo and company name and the contact information and provider name on the other side. I also really like the idea of having the main color dominating on the logo/company side with accent of that same color on the contact side of the card.
Should not have
• Must not be vertical.

```html
<!DOCTYPE html>
<html lang="en">
<head>
<meta charset="utf-8">
<title>Tolvera Hearing Center – Business Card</title>
<link rel="stylesheet" href="https://fonts.googleapis.com/css2?family=Source+Sans+3:wght@300;400;600;700&display=swap">
<style>
  :root {
    --backdrop: #2a2a2a;
    --card: #0f0f0f;
    --card-edge: #1c1c1c;
    --green: #9bcb3c;
    --green-light: #afd23c;
    --white: #ffffff;
    --text: #dbdbdb;
    --text-soft: #cacaca;
    --rule: #3a3a3a;
  }
  * { margin: 0; padding: 0; box-sizing: border-box; }
  html, body {
    width: 1200px; height: 900px; overflow: hidden;
    background: var(--backdrop);
    font-family: "Source Sans 3", "Myriad Pro", sans-serif;
  }
  .canvas {
    position: relative; width: 1200px; height: 900px;
    display: flex; align-items: center; justify-content: center; gap: 40px;
  }
  .card {
    position: relative;
    width: 500px; height: 286px;
    background: var(--card);
    border: 1px solid var(--card-edge);
    border-radius: 20px;
    box-shadow: 0 18px 40px rgba(0,0,0,.45);
    overflow: hidden;
  }

  /* Contact side */
  .card-contact { display: flex; }
  .brand-panel {
    flex: none;
    width: 190px;
    margin: 28px 0;
    height: calc(100% - 56px);
    display: flex; flex-direction: column; align-items: center; justify-content: center;
    gap: 14px;
    border-right: 1px solid var(--rule);
  }
  .brand-dot {
    width: 22px; height: 22px; border-radius: 50%;
    background: var(--green);
  }
  .brand-name-stack {
    color: var(--green);
    font-weight: 600;
    font-size: 22px; line-height: 1.15;
    text-align: center; letter-spacing: .5px;
    text-transform: uppercase;
  }
  .details {
    padding: 42px 0 0 28px;
    color: var(--text);
  }
  .provider {
    font-size: 19px; font-weight: 700; color: var(--white);
    margin-bottom: 8px; white-space: nowrap;
  }
  .provider .surname { color: var(--green); }
  .provider .credentials { font-size: 13px; font-weight: 600; }
  .address { font-size: 14px; line-height: 1.45; color: var(--text-soft); margin-bottom: 16px; }
  .contact-list { list-style: none; font-size: 14px; line-height: 1.5; }
  .contact-list li { display: flex; align-items: center; gap: 10px; white-space: nowrap; }
  .contact-list svg { width: 10px; height: 10px; flex: none; fill: var(--green); }

  /* Brand side */
  .card-brand { display: flex; align-items: center; justify-content: center; gap: 12px; }
  .brand-mark { width: 16px; height: 16px; border-radius: 50%; background: var(--green); }
  .brand-wordmark {
    color: var(--white); font-weight: 300; font-size: 25px;
    letter-spacing: .5px; text-transform: uppercase;
  }
</style>
</head>
<body>
<main class="canvas">

  <section class="card card-contact" aria-label="Business card, contact side">
    <div class="brand-panel">
      <span class="brand-dot"></span>
      <div class="brand-name-stack">Tolvera<br>Hearing<br>Center</div>
    </div>
    <div class="details">
      <p class="provider">Peter <span class="surname">Wolstenby</span><span class="credentials">, Au.D. F/NSB</span></p>
      <p class="address">837 W. Lindell Ave.<br>Brenhurst, OH 44091</p>
      <ul class="contact-list">
        <li>
          <svg viewBox="0 0 10 10" aria-hidden="true"><path d="M2 0.5 L3.6 2.6 L2.8 3.6 C3.4 5 5 6.6 6.4 7.2 L7.4 6.4 L9.5 8 L8.5 9.5 C4.5 9.5 0.5 5.5 0.5 1.5 Z"/></svg>
          (440) 683-5127
        </li>
        <li>
          <svg viewBox="0 0 10 10" aria-hidden="true"><rect x="0.5" y="2" width="9" height="6.5" rx="0.6"/><path d="M0.8 2.3 L5 5.6 L9.2 2.3" fill="none" stroke="#0f0f0f" stroke-width="0.9"/></svg>
          tolverahearing@postvane.com
        </li>
        <li>
          <svg viewBox="0 0 10 10" aria-hidden="true"><circle cx="5" cy="5" r="4.5"/><path d="M0.5 5 H9.5 M5 0.5 C3 3 3 7 5 9.5 M5 0.5 C7 3 7 7 5 9.5" fill="none" stroke="#0f0f0f" stroke-width="0.7"/></svg>
          tolverahearing.com
        </li>
      </ul>
    </div>
  </section>

  <section class="card card-brand" aria-label="Business card, brand side">
    <span class="brand-mark"></span>
    <span class="brand-wordmark">Tolvera Hearing Center</span>
  </section>

</main>
</body>
</html>
```